Corvane Business Cards

Front of business card will have logo, name, address, & telephone number. Back of card will have a list of services provided - Roads, Substation Pads, Temporary Pads, Site Pads, Land Leveling, Powerline Row Cleaning, Land Clearing, Gates, Fencing, Construction Entrances, Excavation, Trenching, Underground Utilities, Directional Boring, Pile Driving. We are a construction company that uses heavy equipment like bulldozers, motor graders/blades, dump trucks, backhoes, hydro axes, & skid loaders. We build roads, pads, & install electric utility lines & waterlines underground. This logo is new. The word "Construction" can be smaller as uploaded 2 example edited logos. We will be using this card design for many employees.
Target Market(s)
Industrial Electric Powerline, Wind Turbine, Solar Panel, & Water Utility companies.
Contact Information for Business Card
Name/Position - Dwayne Halster - Owner
Address: 4875 FM 309
Dellwick, TX 79412
Phone number - (325) 482-5096

```html
<!DOCTYPE html>
<html lang="en">
<head>
<meta charset="utf-8">
<title>Corvane Construction Business Cards</title>
<link href="https://fonts.googleapis.com/css2?family=Marcellus&display=swap" rel="stylesheet">
<style>
  :root {
    --stage: #262626;
    --maroon: #3d141d;
    --maroon-ink: #3d141d;
    --paper: #ffffff;
    --light-ink: #ffffff;
    --card-w: 560px;
    --card-h: 320px;
  }
  * { margin: 0; padding: 0; box-sizing: border-box; }
  html, body {
    width: 1200px; height: 895px; overflow: hidden;
    background: var(--stage);
    font-family: "Marcellus", serif;
  }
  .stage { position: relative; width: 1200px; height: 895px; }
  .card {
    position: absolute;
    width: var(--card-w); height: var(--card-h);
    box-shadow: 0 14px 30px rgba(0,0,0,.55);
  }
  .card-back { left: 150px; top: 95px; background: var(--maroon); color: var(--light-ink); }
  .card-front { left: 490px; top: 480px; background: var(--paper); color: var(--maroon-ink); }

  .services { position: absolute; left: 34px; top: 34px; list-style: none; }
  .services li {
    font-size: 13px; line-height: 16.8px; letter-spacing: .4px;
    display: flex; align-items: center; gap: 9px;
  }
  .services li::before {
    content: ""; width: 7px; height: 7px; background: var(--light-ink); flex: none;
  }

  .wordmark { position: absolute; text-align: center; letter-spacing: 2px; line-height: 1.1; }
  .wordmark .name { display: block; font-size: 40px; }
  .wordmark .sub { display: block; font-size: 22px; letter-spacing: 3px; }
  .card-back .wordmark { right: 40px; top: 100px; }
  .card-front .wordmark { right: 40px; top: 38px; }

  .person { position: absolute; left: 40px; top: 150px; padding-left: 14px; border-left: 2px solid var(--maroon-ink); }
  .person .full-name { font-size: 26px; letter-spacing: 1px; text-transform: uppercase; line-height: 1.1; }
  .person .role { font-size: 15px; letter-spacing: 1px; }

  .contact { position: absolute; left: 56px; top: 232px; font-size: 16px; line-height: 22px; letter-spacing: .6px; }
  .contact .phone { display: flex; align-items: center; gap: 8px; }
  .contact svg { width: 14px; height: 14px; fill: var(--maroon-ink); }
</style>
</head>
<body>
<div class="stage">
  <section class="card card-back">
    <ul class="services">
      <li>Roads</li>
      <li>Substation Pads</li>
      <li>Temporary Pads</li>
      <li>Site Pads</li>
      <li>Land Leveling</li>
      <li>Powerline Row Cleaning</li>
      <li>Land Clearing</li>
      <li>Gates</li>
      <li>Fencing</li>
      <li>Construction Entrances</li>
      <li>Excavation</li>
      <li>Trenching</li>
      <li>Underground Utilities</li>
      <li>Directional Boring</li>
      <li>Pile Driving</li>
    </ul>
    <div class="wordmark">
      <span class="name">CORVANE</span>
      <span class="sub">CONSTRUCTION</span>
    </div>
  </section>

  <section class="card card-front">
    <div class="wordmark">
      <span class="name">CORVANE</span>
      <span class="sub">CONSTRUCTION</span>
    </div>
    <div class="person">
      <p class="full-name">Dwayne Halster</p>
      <p class="role">Owner</p>
    </div>
    <div class="contact">
      <p>4875 FM 309, Dellwick</p>
      <p>TX 79412</p>
      <p class="phone">
        <svg viewBox="0 0 24 24" aria-hidden="true"><path d="M6.6 10.8a15.1 15.1 0 0 0 6.6 6.6l2.2-2.2a1 1 0 0 1 1-.25 11.4 11.4 0 0 0 3.6.57 1 1 0 0 1 1 1V20a1 1 0 0 1-1 1A17 17 0 0 1 3 4a1 1 0 0 1 1-1h3.5a1 1 0 0 1 1 1c0 1.25.2 2.45.57 3.57a1 1 0 0 1-.25 1z"/></svg>
        (325) 482-5096
      </p>
    </div>
  </section>
</div>
</body>
</html>
```